e-commerce store for sport clothing online store "baseball merchandise "web application...

I want to design a UX/UI for my web application website for the online store I will provide you with the following:
1. screen shots of the initial design for the pages>
2. the logo files.
3. The brand guideline file.

the provided files (screen shots) is guideline I want to see CREATIVITY with the UX/UI DESIGN.
PS. PLEASE FOLLOW THE BRANDGUIDE LINE CAREFULLY SPECIALLY THE TYPOGRAPHY & THE COLOR CODES.

PLEASE VISIT THIS WEBSITE brightlane.varomi-qz.com to see more for the screens.

```html
<!DOCTYPE html>
<html lang="en">
<head>
<meta charset="utf-8">
<title>Product Detail</title>
<link href="https://fonts.googleapis.com/css2?family=Titillium+Web:wght@400;600;700&family=Lato:wght@400;700&display=swap" rel="stylesheet">
<style>
:root{
  --navy:#0f2245;
  --crimson:#b3123f;
  --ink:#111111;
  --line:#d6d6d6;
  --muted-btn:#9e9e9e;
  --white:#ffffff;
  --mint-1:#7fe3c6;
  --mint-2:#56cfae;
}
*{box-sizing:border-box;margin:0;padding:0}
html,body{width:1200px;height:3383px;overflow:hidden;background:var(--white)}
.screen{position:relative;width:360px;height:1015px;transform:scale(3.33334);transform-origin:0 0;font-family:"Lato",sans-serif;color:var(--ink);background:var(--white);overflow:hidden}
.app-bar{position:absolute;left:0;top:0;width:360px;height:80px;background:var(--navy)}
.app-bar__title{position:absolute;left:0;right:0;top:28px;text-align:center;color:var(--white);font:700 16px/24px "Titillium Web",sans-serif}
.app-bar__back{position:absolute;left:22px;top:31px}
.app-bar__cart{position:absolute;left:312px;top:28px}
.cart-badge{position:absolute;left:327px;top:24px;width:17px;height:17px;border-radius:50%;background:var(--crimson);color:var(--white);font:700 10px/17px "Lato",sans-serif;text-align:center}
.gallery{position:absolute;left:20px;top:120px;width:321px;height:245px;border-radius:8px;background:var(--white);box-shadow:0 1px 6px rgba(0,0,0,.3);overflow:hidden}
.gallery__photo{position:absolute;inset:0;background:radial-gradient(ellipse 38% 48% at 50% 45%,var(--mint-1) 0%,var(--mint-2) 85%,#f4f4f4 100%)}
.gallery__pager{position:absolute;left:144px;top:220px;width:34px;height:20px;border-radius:10px;background:#000;color:var(--white);font:400 12px/20px "Lato",sans-serif;text-align:center}
.product-name{position:absolute;left:20px;top:406px;font:700 20px/28px "Titillium Web",sans-serif}
.product-price{position:absolute;left:20px;top:437px;color:var(--crimson);font:700 18px/26px "Titillium Web",sans-serif}
.divider{position:absolute;left:10px;width:339px;height:1px;background:var(--line)}
.option-label{position:absolute;left:20px;font:400 15px/20px "Lato",sans-serif}
.color-swatch{position:absolute;left:20px;top:531px;width:48px;height:40px;border:1px solid var(--navy);border-radius:4px;padding:3px}
.color-swatch__photo{width:100%;height:100%;background:linear-gradient(180deg,var(--mint-1),var(--mint-2) 70%,#4a3f6b)}
.size-chip{position:absolute;top:641px;width:23px;height:23px;border-radius:50%;border:1px solid var(--navy);font:400 12px/21px "Lato",sans-serif;text-align:center;color:var(--navy)}
.size-chip--active{background:var(--navy);color:var(--white)}
.qty{position:absolute;top:728px;left:20px;display:flex;gap:8px;align-items:center}
.qty__btn{width:23px;height:23px;border-radius:50%;border:1px solid var(--navy);display:flex;align-items:center;justify-content:center}
.qty__btn--plus{background:var(--navy)}
.qty__value{width:22px;height:22px;border:1px solid var(--line);font:400 12px/20px "Lato",sans-serif;text-align:center}
.description__title{position:absolute;left:20px;top:770px;font:400 16px/22px "Lato",sans-serif}
.description__toggle{position:absolute;left:331px;top:776px}
.description__text{position:absolute;left:20px;width:310px;font:400 14px/17px "Lato",sans-serif}
.action-bar{position:absolute;left:0;top:951px;width:360px;height:64px;background:var(--white);box-shadow:0 -4px 10px rgba(0,0,0,.12)}
.action-bar__status{position:absolute;left:44px;top:21px;color:var(--crimson);font:400 16px/22px "Lato",sans-serif}
.action-bar__button{position:absolute;left:204px;top:10px;width:145px;height:44px;border-radius:4px;background:var(--muted-btn);color:var(--white);font:700 12px/44px "Lato",sans-serif;text-align:center}
</style>
</head>
<body>
<main class="screen">
  <header class="app-bar">
    <svg class="app-bar__back" width="20" height="20" viewBox="0 0 20 20"><path d="M17 10H4M10 3L3 10l7 7" fill="none" stroke="#fff" stroke-width="2.2" stroke-linecap="round" stroke-linejoin="round"/></svg>
    <h1 class="app-bar__title">Product Detail</h1>
    <svg class="app-bar__cart" width="24" height="24" viewBox="0 0 24 24"><path fill="#fff" d="M7 18a2 2 0 1 0 0 4 2 2 0 0 0 0-4zM1 2v2h2l3.6 7.6-1.4 2.4A2 2 0 0 0 7 17h12v-2H7.4l1.1-2h7.5a2 2 0 0 0 1.7-1l3.6-6.5A1 1 0 0 0 20.4 4H5.2l-.9-2H1zm16 16a2 2 0 1 0 0 4 2 2 0 0 0 0-4z"/></svg>
    <span class="cart-badge">1</span>
  </header>

  <section class="gallery">
    <div class="gallery__photo" role="img" aria-label="Product photo of a mint green short sleeve graphic tee worn with patterned shorts"></div>
    <span class="gallery__pager">1/3</span>
  </section>

  <h2 class="product-name">Sunny Shore Graphic Tee</h2>
  <p class="product-price">19.000 KD</p>

  <div class="divider" style="top:482px"></div>
  <p class="option-label" style="top:498px">Color:</p>
  <div class="color-swatch"><div class="color-swatch__photo" role="img" aria-label="Mint colour variant thumbnail"></div></div>

  <div class="divider" style="top:591px"></div>
  <p class="option-label" style="top:606px">Size:</p>
  <span class="size-chip" style="left:20px">S</span>
  <span class="size-chip size-chip--active" style="left:55px">L</span>

  <div class="divider" style="top:681px"></div>
  <p class="option-label" style="top:696px">Qty:</p>
  <div class="qty">
    <span class="qty__btn"><svg width="9" height="9" viewBox="0 0 9 9"><path d="M1 4.5h7" stroke="#0f2245" stroke-width="1.4"/></svg></span>
    <span class="qty__value">2</span>
    <span class="qty__btn qty__btn--plus"><svg width="9" height="9" viewBox="0 0 9 9"><path d="M1 4.5h7M4.5 1v7" stroke="#fff" stroke-width="1.4"/></svg></span>
  </div>

  <h3 class="description__title">Description</h3>
  <svg class="description__toggle" width="14" height="10" viewBox="0 0 14 10"><path d="M2 8l5-5 5 5" fill="none" stroke="#111" stroke-width="2" stroke-linecap="round"/></svg>
  <p class="description__text" style="top:802px">The name says it all!</p>
  <p class="description__text" style="top:839px">Short Sleeve, Featuring hand drawn artwork with super soft pigment dye.</p>

  <div class="action-bar">
    <span class="action-bar__status">Out of Stock</span>
    <span class="action-bar__button">ADD TO CART</span>
  </div>
</main>
</body>
</html>
```